Corporate Business Card

Very professional, Modern, Not to busy, include phone address email, website
(253) 617-4930, 18761 52nd Avenue S, Kent, WA 98047, martin@plumlinegroup.com, varkoworks.com

Target Market(s)

Manufacturing

Industry/Entity Type

Aero, machining, manufacturing, Off road racing

Contact Information for Business Card

Phone, address email, website

```html
<!DOCTYPE html>
<html lang="en">
<head>
<meta charset="utf-8">
<title>Varko Works – Business Card</title>
<link rel="stylesheet" href="https://fonts.googleapis.com/css2?family=Exo+2:wght@400;500;700&family=Orbitron:wght@800&display=swap">
<style>
  :root {
    --backdrop: #7b7b7e;
    --backdrop-light: #8e8e91;
    --card-white: #ffffff;
    --navy: #1b3a8a;
    --deep-blue: #0f2f74;
    --deep-blue-mark: #14398a;
    --signal-red: #e0242c;
  }
  * { box-sizing: border-box; margin: 0; padding: 0; }
  html, body { width: 1200px; height: 781px; overflow: hidden; }
  body {
    background: radial-gradient(ellipse at 45% 40%, var(--backdrop-light), var(--backdrop) 75%);
    font-family: "Exo 2", sans-serif;
    position: relative;
  }
  .card {
    position: absolute;
    box-shadow: 0 6px 18px rgba(0,0,0,.28);
  }
  .card-front {
    left: 150px; top: 128px;
    width: 300px; height: 525px;
    background: var(--card-white);
    padding: 40px 28px 0 34px;
  }
  .brand { display: inline-block; }
  .brand-name {
    font-weight: 700;
    font-size: 30px;
    letter-spacing: 1px;
    color: var(--navy);
    line-height: 1;
    padding-right: 6px;
  }
  .brand-rule { height: 1.5px; background: var(--navy); width: 150px; margin-top: 10px; }
  .contact-block {
    position: absolute;
    right: 28px; top: 290px;
    width: 240px;
    text-align: right;
  }
  .person-name {
    font-family: "Orbitron", sans-serif;
    font-weight: 800;
    font-size: 19px;
    line-height: 1.1;
    color: var(--signal-red);
    letter-spacing: .5px;
  }
  .name-rule { height: 1.5px; background: var(--navy); width: 215px; margin: 6px 0 0 auto; }
  .person-role {
    font-size: 11px;
    line-height: 1.2;
    color: var(--navy);
    margin-top: 4px;
  }
  .address {
    font-size: 12px;
    color: var(--signal-red);
    line-height: 1.35;
    margin-top: 12px;
    margin-right: 4px;
  }
  .lines { margin-top: 16px; }
  .line {
    display: flex; justify-content: flex-end; align-items: center; gap: 6px;
    font-size: 12.5px;
    color: var(--navy);
    line-height: 1.45;
  }
  .line.phone { letter-spacing: 1.5px; font-size: 13px; }
  .line svg { width: 10px; height: 10px; flex: none; }
  .card-back {
    left: 500px; top: 240px;
    width: 525px; height: 300px;
    background: var(--deep-blue);
    display: flex; align-items: center; justify-content: center;
  }
  .back-brand { text-align: center; }
  .back-brand-name {
    font-weight: 700;
    font-size: 46px;
    letter-spacing: 2px;
    color: var(--deep-blue-mark);
  }
  .back-brand-rule { height: 1.5px; background: var(--deep-blue-mark); width: 230px; margin: 10px auto 0; }
</style>
</head>
<body>
  <section class="card card-front" aria-label="Business card front">
    <div class="brand">
      <div class="brand-name">VARKO WORKS</div>
      <div class="brand-rule"></div>
    </div>

    <div class="contact-block">
      <div class="person-name">MARTIN KEDDLE</div>
      <div class="name-rule"></div>
      <div class="person-role">Director</div>
      <div class="address">18761 52nd Avenue S<br>Kent, WA 98047</div>
      <div class="lines">
        <div class="line phone">(253) 617-4930
          <svg viewBox="0 0 10 10" aria-hidden="true"><path d="M2 1 L4 1 L4.6 3 L3.5 3.8 Q4.5 5.8 6.2 6.5 L7 5.4 L9 6 L9 8 Q5 9 1.5 5 Q1 3 2 1Z" fill="var(--signal-red)"/></svg>
        </div>
        <div class="line">martin@plumlinegroup.com
          <svg viewBox="0 0 10 10" aria-hidden="true"><rect x="1" y="2.2" width="8" height="5.6" fill="var(--signal-red)"/><path d="M1 2.4 L5 5.4 L9 2.4" stroke="#fff" stroke-width="0.8" fill="none"/></svg>
        </div>
        <div class="line">varkoworks.com
          <svg viewBox="0 0 10 10" aria-hidden="true"><g fill="none" stroke="var(--signal-red)" stroke-width="0.9"><circle cx="5" cy="5" r="4"/><ellipse cx="5" cy="5" rx="1.8" ry="4"/><path d="M1 5 H9 M1.7 3 H8.3 M1.7 7 H8.3"/></g></svg>
        </div>
      </div>
    </div>
  </section>

  <section class="card card-back" aria-label="Business card back">
    <div class="back-brand">
      <div class="back-brand-name">VARKO WORKS</div>
      <div class="back-brand-rule"></div>
    </div>
  </section>
</body>
</html>
```